Construction material supplies company business card ****

1. Full company name “K T Masonry Works Ltd”
I am after a Business card design for the company as a whole. We are better known in Solomon Islands as “K T Masonry” for short.

We are a building materials supplier of
Ready Mixed Concrete, Bricks and Blocks,
Quarry products- gravel, aggregates, sand etc.
Cement distributor/retailer of reputable brands.
Other prefab concrete products. Culverts, wave breakers, concrete retaining blocks etc.

2. Competitive Advantage over Competition: Quality, efficient, professional, dependable, reliable

3. We want people to feel trust worthy, high quality, strong when they see our brand

5. No preference to color. Maybe more sturdy and corporate. Not fancy.

Industry/Entity Type

CONSTRUCTION SUPPLY

Contact Information for Business Card

Name, Position, office phone mob phone, email

Requirements
Must have
• the company logo
Nice to have
• would like to see a mixture of designs, of with logo only and also with simple graphic designs to bring out the company whilst still have the strong sturdy professional feeling

```html
<!DOCTYPE html>
<html lang="en">
<head>
<meta charset="utf-8">
<title>K T Masonry – Business Card</title>
<link href="https://fonts.googleapis.com/css2?family=Roboto:wght@400;500;700&display=swap" rel="stylesheet">
<style>
  :root {
    --page-bg: #2b2b2b;
    --card-light: #ececec;
    --card-mid: #d9d9d9;
    --brand-blue: #1f3f66;
    --band-blue: #2b4c72;
    --text-light: #f2f4f7;
  }
  * { margin: 0; padding: 0; box-sizing: border-box; }
  html, body {
    width: 1200px; height: 1138px; overflow: hidden;
    background: var(--page-bg);
    font-family: "Roboto", Arial, sans-serif;
  }
  .canvas { position: relative; width: 1200px; height: 1138px; }

  .card {
    position: absolute;
    border-radius: 14px;
    background: radial-gradient(ellipse at 40% 40%, var(--card-light) 0%, var(--card-mid) 100%);
    overflow: hidden;
    color: var(--brand-blue);
  }
  .card-front { left: 274px; top: 186px; width: 623px; height: 376px; }
  .card-back  { left: 276px; top: 608px; width: 618px; height: 374px; }

  /* Front */
  .front-brand {
    position: absolute; left: 0; right: 0; top: 66px;
    display: flex; align-items: center; justify-content: center; gap: 22px;
  }
  .brand-square { width: 52px; height: 52px; background: var(--brand-blue); }
  .brand-name {
    font-weight: 700; font-size: 54px; letter-spacing: 2px; line-height: 1;
    color: var(--brand-blue);
  }
  .service-band {
    position: absolute; left: 0; right: 0; top: 213px; height: 79px;
    background: var(--band-blue);
  }
  .intro-pill {
    position: absolute; left: 137px; top: 186px; width: 349px; height: 42px;
    background: var(--band-blue);
    border: 2px solid #f4f4f4; border-radius: 21px;
    color: var(--text-light); font-size: 16px;
    display: flex; align-items: center; justify-content: center;
  }
  .service-list {
    position: absolute; left: 0; right: 0; top: 240px;
    text-align: center; color: var(--text-light);
    font-size: 16px; line-height: 22px;
  }
  .extra-services {
    position: absolute; left: 0; right: 0; top: 307px;
    text-align: center; font-size: 16px; line-height: 24px;
    color: var(--brand-blue);
  }

  /* Back */
  .person { position: absolute; left: 46px; top: 40px; }
  .person-name { font-size: 23px; font-weight: 700; line-height: 28px; }
  .person-role { font-size: 16px; line-height: 22px; }
  .contact-list { position: absolute; left: 46px; top: 200px; list-style: none; }
  .contact-list li {
    display: flex; align-items: center; gap: 14px;
    height: 26px; font-size: 16px;
  }
  .contact-list svg { width: 16px; height: 16px; fill: var(--brand-blue); }
  .address { position: absolute; left: 46px; top: 283px; font-size: 16px; line-height: 26px; }
  .back-brand {
    position: absolute; left: 351px; width: 220px; top: 190px;
    display: flex; flex-direction: column; align-items: center; gap: 20px;
  }
  .back-brand .brand-square { width: 62px; height: 62px; }
  .back-brand .brand-name { font-size: 34px; letter-spacing: 1px; }
</style>
</head>
<body>
<div class="canvas">

  <section class="card card-front">
    <div class="front-brand">
      <span class="brand-square"></span>
      <span class="brand-name">K T MASONRY</span>
    </div>
    <div class="service-band"></div>
    <div class="intro-pill">We are a building materials supplier of</div>
    <p class="service-list">
      Ready Mixed Concrete, Bricks and Blocks, Quarry Products<br>
      Quarry Products:- Gravel, Aggregates, Sand Etc.
    </p>
    <p class="extra-services">
      Cement Distributor/Retailer of Reputable Brands.<br>
      Other Concrete Products Culverts, Wave Breakers, Concrete Retaining Blocks
    </p>
  </section>

  <section class="card card-back">
    <div class="person">
      <p class="person-name">Daniel Foster</p>
      <p class="person-role">Managing Director</p>
    </div>
    <ul class="contact-list">
      <li>
        <svg viewBox="0 0 16 16" aria-hidden="true"><path d="M2 4c0-1 1-2 6-2s6 1 6 2v2h-3V4.5H5V6H2zM4 7h8l2 6H2zm4 1.5a2 2 0 100 4 2 2 0 000-4z"/></svg>
        <span>000 0000 0000</span>
      </li>
      <li>
        <svg viewBox="0 0 16 16" aria-hidden="true"><path d="M1 3h14v10H1zm1.5 1.5v.4L8 9l5.5-4.1v-.4zM2.5 6.7v4.8h11V6.7L8 10.8z"/></svg>
        <span>daniel@ktmasonry.com</span>
      </li>
      <li>
        <svg viewBox="0 0 16 16" aria-hidden="true"><path d="M8 1a7 7 0 100 14A7 7 0 008 1zm-1 1.8v2.7H4.6A5.5 5.5 0 017 2.8zm2 0a5.5 5.5 0 012.4 2.7H9zM2.6 7h4.4v2H2.6a5.5 5.5 0 010-2zm6.4 0h4.4a5.5 5.5 0 010 2H9zm-4.4 3.5H7v2.7a5.5 5.5 0 01-2.4-2.7zm4.4 0h2.4A5.5 5.5 0 019 13.2z"/></svg>
        <span>www.ktmasonry.com</span>
      </li>
    </ul>
    <p class="address">18 Harbour Rd., Point Cruz,<br>Honiara, SB 00100</p>
    <div class="back-brand">
      <span class="brand-square"></span>
      <span class="brand-name">K T MASONRY</span>
    </div>
  </section>

</div>
</body>
</html>
```